Q&J RESTORATION

I want a brochure similiar to the example i've attached.
My company name is Q&J Restoration. The website is: Q-J-Restoration.example.
The phone number is 919.555.0147.

I don't like the "yellow" being the main color of the example so I'm open to suggestions. I want something CLEAN & Simple, like our logo . This will be a bi fold brochure

```html
<!DOCTYPE html>
<html lang="en">
<head>
<meta charset="utf-8">
<title>Q&amp;J Restoration – Bi-fold Brochure</title>
<link rel="stylesheet" href="https://fonts.googleapis.com/css2?family=Bebas+Neue&family=Montserrat:wght@400;500;600&display=swap">
<style>
  :root {
    --page-bg: #d2d1d2;
    --paper: #ffffff;
    --navy: #0a5597;
    --bright: #0a86d4;
    --ink: #0b0b0b;
    --overlay: #0f5a9c;
    --photo-dark: #1e4f86;
    --photo-light: #c9d8e8;
    --fold-shade: #c4c6c9;
  }
  * { box-sizing: border-box; margin: 0; padding: 0; }
  html, body { width: 770px; height: 1200px; overflow: hidden; }
  body { background: var(--page-bg); position: relative; font-family: "Montserrat", sans-serif; }

  .spread { position: absolute; left: 90px; width: 602px; height: 464px; background: var(--paper); overflow: hidden; }
  .spread--outside { top: 110px; }
  .spread--inside { top: 630px; }
  .panel { position: absolute; top: 0; width: 301px; height: 464px; overflow: hidden; }
  .panel--left { left: 0; }
  .panel--right { left: 301px; }
  .panel svg.shapes { position: absolute; inset: 0; }

  .headline { font-family: "Bebas Neue", sans-serif; line-height: 0.92; position: absolute; }

  /* Outside – back panel */
  .claim { left: 0; width: 301px; top: 266px; text-align: center; }
  .claim__ask { color: var(--ink); font-size: 43px; }
  .claim__answer { color: var(--navy); font-size: 52px; line-height: 0.88; margin-top: -2px; }
  .call-text { position: absolute; left: 52px; top: 410px; width: 236px; text-align: center; white-space: nowrap;
    font-family: "Bebas Neue", sans-serif; font-size: 26px; line-height: 1; color: #fff; letter-spacing: 0.3px; }
  .website { position: absolute; left: 0; width: 301px; top: 446px; text-align: center;
    font-family: "Montserrat", sans-serif; font-weight: 500; font-size: 8px; color: var(--navy); letter-spacing: 0.4px; }

  /* Outside – front cover */
  .fold-shade { position: absolute; left: 0; top: 0; width: 110px; height: 464px;
    background: linear-gradient(to right, var(--fold-shade), rgba(255,255,255,0)); }
  .brand { position: absolute; left: 130px; top: 28px; width: 150px; height: 44px;
    display: flex; align-items: center; gap: 7px; color: #fff; }
  .brand__mark { width: 10px; height: 10px; background: #fff; }
  .brand__name { font-family: "Montserrat", sans-serif; font-weight: 500; font-size: 14px; letter-spacing: 0.5px; }
  .tagline { left: 40px; width: 230px; top: 132px; text-align: center; font-size: 56px; line-height: 0.93; }
  .tagline .dark { color: var(--ink); }
  .tagline .blue { color: var(--bright); font-size: 60px; }

  /* Inside – left panel */
  .damage { left: 16px; top: 42px; color: var(--navy); font-size: 50px; line-height: 0.9; }
  .after { position: absolute; left: 16px; top: 190px; font-family: "Bebas Neue", sans-serif; font-size: 21px; line-height: 0.95; color: var(--ink); }
  .benefits { position: absolute; left: 16px; top: 244px; list-style: none; width: 250px; }
  .benefit { position: relative; padding-left: 55px; overflow: hidden; }
  .benefit:nth-child(1) { height: 57px; }
  .benefit:nth-child(2) { height: 48px; }
  .benefit:nth-child(3) { height: 52px; }
  .benefit:nth-child(4) { height: 56px; }
  .benefit__icon { position: absolute; left: 0; top: 0; width: 43px; height: 38px; }
  .benefit__title { font-family: "Bebas Neue", sans-serif; font-size: 21px; color: var(--bright); line-height: 1; }
  .benefit__text { font-size: 7.2px; line-height: 1.15; color: #222; margin-top: 1px; }

  /* Inside – right panel */
  .team-photo { position: absolute; inset: 0;
    background: linear-gradient(160deg, #2a6aa8 0%, var(--overlay) 55%, #0c4f8c 100%); }
  .ghost { position: absolute; left: 0; width: 301px; top: 276px; text-align: center;
    color: rgba(255,255,255,0.18); font-size: 54px; letter-spacing: 5px; line-height: 1.09; }
</style>
</head>
<body>

<!-- Outside spread -->
<section class="spread spread--outside">
  <div class="panel panel--left">
    <svg class="shapes" width="301" height="464" viewBox="0 0 301 464">
      <polygon points="0,0 300,0 272,110 215,150 140,190 110,190 0,106" fill="var(--photo-dark)" role="img" aria-label="Photo of restoration workers inspecting a damaged wall, blue tint"/>
      <polygon points="157,96 258,96 297,172 258,248 157,248 126,172" fill="var(--photo-light)" stroke="#4f7fae" stroke-width="5" stroke-linejoin="round" role="img" aria-label="Photo of a worker in overalls kneeling to measure a floor"/>
      <g class="call-bar">
        <polygon points="13,423 21,408 38,408 46,423 38,438 21,438" fill="var(--navy)" stroke="var(--navy)" stroke-width="3" stroke-linejoin="round"/>
        <path d="M24,416 q-1,3 1,7 t7,7 l3,-2.5 -3.5,-3 -2,1.5 q-2.5,-1.5 -4,-4 l1.5,-2 -3,-3.5 z" fill="#fff"/>
        <path d="M31,417 a4,4 0 0 1 3,3 M31,414 a7,7 0 0 1 6,6" stroke="#fff" stroke-width="1.2" fill="none"/>
        <polygon points="56,408 284,408 277,438 49,438" fill="var(--navy)" stroke="var(--navy)" stroke-width="4" stroke-linejoin="round"/>
      </g>
    </svg>
    <div class="headline claim">
      <div class="claim__ask">Insurance Claim?</div>
      <div class="claim__answer">We’re on<br>your team</div>
    </div>
    <div class="call-text">Call now! (919) 555 0147</div>
    <div class="website">Q-J-Restoration.example</div>
  </div>

  <div class="panel panel--right">
    <div class="fold-shade"></div>
    <svg class="shapes" width="301" height="464" viewBox="0 0 301 464">
      <path d="M80,0 H301 V92 L270,120 Q252,126 230,120 L125,90 Q108,84 102,66 Z" fill="var(--bright)"/>
      <polygon points="38,300 228,300 266,380 266,464 0,464 0,360" fill="var(--photo-light)" stroke="#2f6aa6" stroke-width="6" stroke-linejoin="round" role="img" aria-label="Photo of a modern kitchen with a flooded floor"/>
      <path d="M301,322 Q275,322 255,345 L175,430 Q162,450 175,464 H301 Z" fill="var(--bright)" opacity="0.85"/>
    </svg>
    <div class="brand"><span class="brand__mark"></span><span class="brand__name">Q&amp;J Restoration</span></div>
    <div class="headline tagline">
      <div class="dark">Build</div>
      <div class="blue">Renovate</div>
      <div class="dark">Restore</div>
    </div>
  </div>
</section>

<!-- Inside spread -->
<section class="spread spread--inside">
  <div class="panel panel--left">
    <svg class="shapes" width="301" height="464" viewBox="0 0 301 464">
      <path d="M136,0 H301 V38 L270,68 Q250,82 220,78 L170,70 Q150,64 146,42 Z" fill="var(--bright)"/>
      <polygon points="205,8 301,8 301,240 276,246 168,140 205,8" fill="#d8e6f4" stroke="var(--bright)" stroke-width="4" stroke-linejoin="round" role="img" aria-label="Photo of rolled architectural blueprints"/>
    </svg>
    <div class="headline damage">Water<br>or mold<br>damage?</div>
    <div class="after">What happens<br>after the cleanup?</div>
    <ul class="benefits">
      <li class="benefit">
        <svg class="benefit__icon" viewBox="0 0 43 38"><polygon points="11,2 32,2 41,19 32,36 11,36 2,19" fill="var(--photo-light)" stroke="var(--navy)" stroke-width="2.5" role="img" aria-label="Photo of an adjuster with a client"/></svg>
        <div class="benefit__title">Adjuster’s Inspection</div>
        <p class="benefit__text">Feel Confident. Be sure you received a fair and accurate assessment &amp; repair of all damages with our team’s use of industry leading estimating systems and On-Site Review.</p>
      </li>
      <li class="benefit">
        <svg class="benefit__icon" viewBox="0 0 43 38"><polygon points="11,2 32,2 41,19 32,36 11,36 2,19" fill="var(--photo-light)" stroke="var(--navy)" stroke-width="2.5" role="img" aria-label="Photo of a clock"/></svg>
        <div class="benefit__title">Timely Settlement</div>
        <p class="benefit__text">Don’t wait. Minimize the hassle of long processing times from Estimate to settlement when you team up with an insurance Repair Specialist.</p>
      </li>
      <li class="benefit">
        <svg class="benefit__icon" viewBox="0 0 43 38"><polygon points="11,2 32,2 41,19 32,36 11,36 2,19" fill="var(--photo-light)" stroke="var(--navy)" stroke-width="2.5" role="img" aria-label="Photo of a craftsman at work"/></svg>
        <div class="benefit__title">Superior Craftsmanship</div>
        <p class="benefit__text">Don’t settle for satisfactory. Our team is committed to the highest standards of excellence every step of the way. Trust us when we say that we’ll make your smile</p>
      </li>
      <li class="benefit">
        <svg class="benefit__icon" viewBox="0 0 43 38"><polygon points="11,2 32,2 41,19 32,36 11,36 2,19" fill="var(--photo-light)" stroke="var(--navy)" stroke-width="2.5" role="img" aria-label="Photo of a house roof"/></svg>
        <div class="benefit__title">Under One Roof</div>
        <p class="benefit__text">Don’t worry. You won’t need to arrange<br>meetings with multiple contractors we’ll<br>take care of everything from demo to final cleanup.</p>
      </li>
    </ul>
  </div>

  <div class="panel panel--right">
    <div class="team-photo" role="img" aria-label="Photo of two contractors inspecting a ceiling on a renovation site, blue tint"></div>
    <div class="headline ghost">Build<br>Renovate<br>Restore</div>
  </div>
</section>

</body>
</html>
```